VENTURE CAPITAL GROUP BUSINESS CARD DESIGN

Venture Capital Group based in SF looking for a bold business card design. No trendy colour explosion, 3D effects etc. Just "simple" optical effects. Works on your brain, keeps your eye focused and sticks to your mind.
Target Market(s)
Technology startups
Industry/Entity Type
Venture Capital
Contact Information for Business Card
DESMOND WHITLAKE
MANAGING PARTNER
187 FENWORTH ST SAN FRANCISCO, CA 94187
415.555.0142 O
415.555.0147 F
415.555.0193 C
desmond@veldtmoorcapital.ventures

```html
<!DOCTYPE html>
<html lang="en">
<head>
<meta charset="utf-8">
<title>Veldtmoor Capital Group — Business Card</title>
<link rel="stylesheet" href="https://fonts.googleapis.com/css2?family=Cinzel:wght@400&family=Merriweather:wght@400;700&family=Source+Sans+3:wght@400&display=swap">
<style>
  :root {
    --backdrop: #a9a7a8;
    --green: #2f9b40;
    --green-light: #57b84c;
    --green-dark: #19703a;
    --green-mark: #3fae4a;
    --paper: #fbfbfb;
    --ink: #5a5a5a;
    --ink-soft: #6b6b6b;
    --rule: #e1e1e1;
    --steel: #9d9d9f;
    --white: #ffffff;
  }
  * { box-sizing: border-box; margin: 0; padding: 0; }
  html, body { width: 1200px; height: 1200px; overflow: hidden; }
  body { background: var(--backdrop); position: relative; }

  .card {
    position: absolute;
    left: 243px;
    width: 714px;
    height: 420px;
    overflow: hidden;
  }
  .card--front {
    top: 117px;
    background: linear-gradient(180deg, var(--green-light) 0%, var(--green) 55%, var(--green-dark) 100%);
  }
  .card--back { top: 644px; background: var(--paper); }

  /* Front */
  .front-mark {
    position: absolute;
    left: 276px; top: 87px;
    width: 160px; height: 160px;
    border-radius: 50%;
    background: var(--green-mark);
  }
  .front-lockup {
    position: absolute;
    left: 0; right: 0; top: 262px;
    text-align: center;
    color: var(--white);
    font-family: "Cinzel", serif;
    font-weight: 400;
  }
  .front-lockup .wordmark { font-size: 46px; letter-spacing: 1px; line-height: 1; }
  .front-lockup .tagline { font-size: 14px; letter-spacing: 7px; margin-top: 4px; line-height: 1; }

  /* Back: brand side */
  .back-mark {
    position: absolute;
    left: 92px; top: 92px;
    width: 138px; height: 138px;
    border-radius: 50%;
    background: #ececec;
  }
  .back-lockup {
    position: absolute;
    left: 20px; width: 302px; top: 254px;
    text-align: center;
    color: var(--green);
    font-family: "Cinzel", serif;
    font-weight: 400;
  }
  .back-lockup .wordmark { font-size: 34px; line-height: 1; }
  .back-lockup .tagline { font-size: 10px; letter-spacing: 5px; margin-top: 2px; line-height: 1; }

  .divider {
    position: absolute;
    left: 326px; top: 60px;
    width: 1px; height: 272px;
    background: var(--rule);
  }

  /* Back: contact side */
  .contact { position: absolute; left: 360px; top: 92px; }
  .contact .name {
    font-family: "Merriweather", serif;
    font-weight: 700;
    font-size: 24px;
    color: var(--ink);
    line-height: 1.1;
  }
  .contact .role {
    font-family: "Merriweather", serif;
    font-size: 15px;
    color: var(--ink-soft);
    margin-top: 2px;
  }
  .contact-list {
    list-style: none;
    margin-top: 18px;
    font-family: "Source Sans 3", sans-serif;
    font-size: 18px;
    color: var(--ink);
  }
  .contact-list li { display: flex; align-items: center; height: 23px; }
  .contact-list svg { width: 18px; height: 16px; margin-right: 15px; fill: var(--green); }
  .address {
    margin-top: 10px;
    font-family: "Source Sans 3", sans-serif;
    font-size: 18px;
    color: var(--ink);
  }

  .bands { position: absolute; left: 0; bottom: 0; width: 714px; height: 55px; }
  .web {
    position: absolute;
    left: 360px; bottom: 16px;
    font-family: "Source Sans 3", sans-serif;
    font-size: 18px;
    color: var(--white);
  }
</style>
</head>
<body>

<section class="card card--front" aria-label="Card front">
  <div class="front-mark"></div>
  <div class="front-lockup">
    <div class="wordmark">VELDTMOOR</div>
    <div class="tagline">CAPITAL GROUP</div>
  </div>
</section>

<section class="card card--back" aria-label="Card back">
  <div class="back-mark"></div>
  <div class="back-lockup">
    <div class="wordmark">VELDTMOOR</div>
    <div class="tagline">CAPITAL GROUP</div>
  </div>

  <div class="divider"></div>

  <div class="contact">
    <div class="name">Desmond Whitlake</div>
    <div class="role">Managing Partner</div>
    <ul class="contact-list">
      <li>
        <svg viewBox="0 0 18 16" aria-label="Office"><path d="M1 6c0-3 4-5 8-5s8 2 8 5l-3 1-1-2c-2-.6-6-.6-8 0L4 7zM4 8h10l2 7H2z"/></svg>
        415.555.0142
      </li>
      <li>
        <svg viewBox="0 0 18 16" aria-label="Fax"><path d="M5 1h8v4H5zM1 6h16v7h-3v-3H4v3H1zM5 11h8v4H5z"/></svg>
        415.555.0147
      </li>
      <li>
        <svg viewBox="0 0 18 16" aria-label="Mobile"><path d="M5 0h8v16H5zM6.5 2v10h5V2z"/></svg>
        415.555.0193
      </li>
      <li>
        <svg viewBox="0 0 18 16" aria-label="Email"><path d="M0 2h18v12H0zM1.5 3.5 9 9l7.5-5.5v-.2H1.5z"/></svg>
        desmond@veldtmoorcapital.ventures
      </li>
    </ul>
    <div class="address">187 Fenworth St San Francisco, CA 94187</div>
  </div>

  <svg class="bands" viewBox="0 0 714 55" preserveAspectRatio="none" aria-hidden="true">
    <defs>
      <linearGradient id="steel-band" x1="0" x2="1">
        <stop offset="0" stop-color="#b5b5b7"/>
        <stop offset="1" stop-color="#8e8e90"/>
      </linearGradient>
      <linearGradient id="green-band" x1="0" x2="1">
        <stop offset="0" stop-color="#2f9b40"/>
        <stop offset="1" stop-color="#27843a"/>
      </linearGradient>
    </defs>
    <rect x="0" y="27" width="320" height="28" fill="url(#steel-band)"/>
    <polygon points="330,0 714,0 714,55 294,55" fill="url(#green-band)"/>
  </svg>
  <div class="web">www.veldtmoorcapital.ventures</div>
</section>

</body>
</html>
```